The Wager a non-fiction book on mindfulness COVER design needed

A non-fiction book about active mindfulness.
The Wager includes 21 different daily 'dares' which are action based activities to generate positive mindfulness - to become more contented with life.
Based on the teeaching of the New Thought movements of the early 20th century, think The Hidden Key, Plan and Become Wealthy.
The book is positive and uplifting. It fits into the self-help / spiritual / health segments. It skews female 40 to 50 year olds.
Think fresh colours like a bold orange or bright green.
What needs to be on the cover:
TITLE: The Wager
AUTHOR: Martin Fenwick
BLURB: Get clarity, focus, and a new zest for life by following The Wager for just 21 days.
Women 40-50 english speaking
Self-help / Health

```html
<!DOCTYPE html>
<html lang="en">
<head>
<meta charset="utf-8">
<title>The Wager — Book Cover</title>
<link rel="stylesheet" href="https://fonts.googleapis.com/css2?family=Bebas+Neue&display=swap">
<style>
  :root {
    --cover-teal: #22bec8;
    --accent-yellow: #f4ee32;
    --ink-white: #ffffff;
    --stage-bg: #eeece8;
    --display-font: "Bebas Neue", "Oswald", sans-serif;
  }
  html, body {
    margin: 0;
    padding: 0;
    width: 1200px;
    height: 1000px;
    overflow: hidden;
    background: var(--stage-bg);
  }
  .canvas {
    position: relative;
    width: 1200px;
    height: 1000px;
  }
  .book-cover {
    position: absolute;
    left: 282px;
    top: 26px;
    width: 635px;
    height: 947px;
    display: block;
  }
  .cover-ground { fill: var(--cover-teal); }
  .divider-white { fill: var(--ink-white); }
  .divider-yellow { fill: var(--accent-yellow); }
  .author-name {
    font-family: var(--display-font);
    font-size: 50px;
    fill: var(--accent-yellow);
    letter-spacing: 6px;
  }
  .title-the {
    font-family: var(--display-font);
    font-size: 194px;
    fill: var(--ink-white);
  }
  .title-wager {
    font-family: var(--display-font);
    font-size: 294px;
    fill: var(--accent-yellow);
  }
  .blurb {
    font-family: var(--display-font);
    font-size: 31px;
    fill: var(--ink-white);
    letter-spacing: 0.5px;
  }
  .blurb .highlight { fill: var(--accent-yellow); }
  .figure-climber { fill: var(--ink-white); opacity: 0.85; }
  .figure-walker { fill: var(--accent-yellow); opacity: 0.9; }
</style>
</head>
<body>
<main class="canvas">
  <svg class="book-cover" viewBox="0 0 635 947" xmlns="http://www.w3.org/2000/svg" aria-label="The Wager by Martin Fenwick, book cover">
    <rect class="cover-ground" x="0" y="0" width="635" height="947"/>

    <text class="author-name" x="66" y="100" textLength="350" lengthAdjust="spacingAndGlyphs">MARTIN FENWICK</text>

    <rect class="divider-white" x="474" y="0" width="9" height="240"/>

    <rect class="figure-climber" x="346" y="145" width="105" height="95" rx="24"
          role="img" aria-label="Silhouette of a woman with a briefcase stepping up onto the title"/>

    <text class="title-the" x="338" y="370" textLength="230" lengthAdjust="spacingAndGlyphs">THE</text>

    <text class="title-wager" x="66" y="612" textLength="502" lengthAdjust="spacingAndGlyphs">WAGER</text>

    <rect class="divider-yellow" x="361" y="600" width="13" height="347"/>

    <rect class="figure-walker" x="180" y="626" width="176" height="321" rx="40"
          role="img" aria-label="Silhouette of a woman in a dress walking with a phone and handbag"/>

    <text class="blurb">
      <tspan x="398" y="692">GET CLARITY<tspan class="highlight">,</tspan></tspan>
      <tspan x="398" y="727">FOCUS<tspan class="highlight">,</tspan> AND</tspan>
      <tspan x="398" y="763">A NEW ZEST</tspan>
      <tspan x="398" y="798">FOR LIFE</tspan>
      <tspan x="398" y="833">BY FOLLOWING</tspan>
      <tspan x="398" y="868" class="highlight">THE WAGER</tspan>
      <tspan x="398" y="904">FOR JUST 21 DAYS</tspan>
    </text>
  </svg>
</main>
</body>
</html>
```